Dental Practice Billboard Design

We are a newer dental practice in need of a simple but appealing billboard for our growing dental practice to attract new patients. The practice is owned by husband and wife dentists and is family friendly in a small town in Kentucky. We try to be very friendly and caring to our patients. Would prefer a blue background for the billboard and our tooth logo to be prominent. We are partial to the Patua One font used in the image below but please feel free to tweak it as you deem necessary. The shape of the uppercase D and lowercase g are why we like that font, so fonts with a similarly shaped “D” and “g” would work as well. Please include our phone number (555) 847-1390. Please see our website Harlowbrookdentistry.example for more info on the practice if needed. Thank you! Looking forward to seeing your creation.
Updates

The dimensions will be 12ft x 24ft (3.6576m x 7.3152m). Apologies for not including this in the original prompt. Thank you all for your submissions.

Industry/Entity Type

Dental

Font styles to use
Other font styles liked:
• Patua One

Colors
0054AA
0677BA
7BADD7
CADEEF
E8F1F8
0094D4
00A9DD
6FCCEA
C7EBF8
E9F6FB
00AB8E
00BBA5
67D7C9
C6EFE9
E9F9F6
59FF00
82FF00
B8FF75
E3FFCB
F4FFEA

Requirements
Must have
• Phone number, website, Logo, Practice name “Harlow Brook Dentistry”
Should not have
• A tagline or slogan

```html
<!DOCTYPE html>
<html lang="en">
<head>
<meta charset="utf-8">
<title>Harlow Brook Dentistry Billboard</title>
<link href="https://fonts.googleapis.com/css2?family=Patua+One&family=Fjalla+One&display=swap" rel="stylesheet">
<style>
  :root {
    --brand-blue: #2a52a0;
    --deep-blue: #1d4690;
    --brand-green: #22b24c;
    --light-green: #6cc644;
    --white: #ffffff;
    --stage: #eef1f5;
  }
  * { box-sizing: border-box; margin: 0; padding: 0; }
  html, body {
    width: 1200px; height: 900px; overflow: hidden;
    background: var(--stage);
  }
  .billboard {
    position: absolute; left: 40px; top: 170px;
    width: 1120px; height: 560px;
    background: var(--white);
    overflow: hidden;
    box-shadow: 0 6px 24px rgba(0,0,0,0.15);
  }
  .side-shapes { position: absolute; left: 0; top: 0; width: 480px; height: 560px; }
  .team-photo {
    position: absolute; left: 56px; top: 70px; width: 420px; height: 490px;
    border-radius: 210px 210px 0 0;
    background: linear-gradient(160deg, #c98f6e 0%, #f3f3f3 35%, #e7e9ec 60%, #2b2b2b 100%);
  }
  .practice-name {
    position: absolute; left: 500px; top: 50px;
    display: flex; align-items: center; gap: 24px;
  }
  .name-dot {
    flex: none;
    width: 110px; height: 110px; border-radius: 50%;
    background: var(--brand-blue);
  }
  .name-text {
    font-family: 'Patua One', serif; color: var(--brand-blue);
    white-space: nowrap;
  }
  .name-main { display: block; font-size: 76px; line-height: 1; }
  .name-sub { display: block; font-size: 46px; line-height: 1.1; padding-left: 4px; }
  .call-band {
    position: absolute; left: 390px; top: 270px; width: 730px; height: 100px;
    border-radius: 36px 0 0 36px;
    background: linear-gradient(90deg, var(--brand-green), var(--light-green));
    display: flex; align-items: center; padding-left: 40px;
    font-family: 'Fjalla One', sans-serif; font-size: 70px;
    color: var(--white); white-space: nowrap;
  }
  .website {
    position: absolute; left: 500px; top: 420px;
    display: flex; align-items: center; gap: 14px;
    font-family: 'Patua One', serif; font-size: 30px;
    color: var(--deep-blue); white-space: nowrap;
  }
  .website svg { width: 28px; height: 28px; flex: none; }
</style>
</head>
<body>
  <main class="billboard">
    <svg class="side-shapes" viewBox="0 0 480 560" aria-hidden="true">
      <defs>
        <linearGradient id="greenFade" x1="0" y1="0" x2="0" y2="1">
          <stop offset="0" stop-color="#22b24c"/>
          <stop offset="1" stop-color="#6cc644"/>
        </linearGradient>
      </defs>
      <rect x="0" y="0" width="480" height="560" fill="url(#greenFade)"/>
      <path d="M70 0 H480 V560 H220 C110 430 70 250 70 0 Z" fill="#1d4690"/>
      <path d="M330 0 H480 V560 H330 C250 420 250 140 330 0 Z" fill="#ffffff"/>
    </svg>
    <div class="team-photo" role="img" aria-label="Photo of the two smiling dentists in white coats"></div>

    <div class="practice-name">
      <span class="name-dot"></span>
      <h1 class="name-text">
        <span class="name-main">Harlow Brook</span>
        <span class="name-sub">Dentistry</span>
      </h1>
    </div>

    <div class="call-band">CALL : (555) 847-1390</div>

    <div class="website">
      <svg viewBox="0 0 24 24" aria-hidden="true">
        <path d="M3 3 L21 9 L14 11.5 L21 18.5 L18.5 21 L11.5 14 L9 21 Z" fill="#1d4690"/>
      </svg>
      <span>www.harlowbrookdentistry.example</span>
    </div>
  </main>
</body>
</html>
```